Business Card Design for Training Business

Clear Path Coaching is a new business that delivers training and other services with a focus on topics related to mental health and wellbeing, for example, Wellmind Response Course, Resilience etc. We have a strong focus on evidence-based psychology and neuroscience. I have a logo which I will upload with the brief, so please consider colours that work well with the logo.
Target Market(s)
Adults, workplaces (particularly government and not-for-profits)
Industry/Entity Type
Business
Contact Information for Business Card
Head Strong TrainingSamantha SellwoodDirector0438 770 850sam@headstrongtraining.com.auwww.headstrongtraining.com.au

```html
<!DOCTYPE html>
<html lang="en">
<head>
<meta charset="utf-8">
<title>Clear Path Coaching – Business Card</title>
<link rel="stylesheet" href="https://fonts.googleapis.com/css2?family=Open+Sans:wght@300;400;700&display=swap">
<style>
  :root {
    --stage: #e9e7e3;
    --card-black: #0b0c0d;
    --card-sheen: #1c1e20;
    --teal: #2fc3c6;
    --teal-deep: #1fa7ab;
    --ink-white: #f4f5f5;
    --ink-grey: #b9bdbf;
  }
  * { margin: 0; padding: 0; box-sizing: border-box; }
  html, body {
    width: 1200px;
    height: 1022px;
    overflow: hidden;
    background: var(--stage);
    font-family: "Open Sans", Arial, sans-serif;
  }
  .stage {
    width: 1200px;
    height: 1022px;
    display: flex;
    align-items: center;
    justify-content: center;
  }
  .card {
    position: relative;
    width: 1000px;
    height: 572px;
    border-radius: 18px;
    overflow: hidden;
    background: linear-gradient(160deg, var(--card-sheen) 0%, var(--card-black) 45%, var(--card-black) 100%);
    box-shadow: 0 18px 40px rgba(0,0,0,0.28);
  }
  .brand {
    position: absolute;
    left: 72px;
    top: 200px;
    display: flex;
    align-items: center;
    gap: 26px;
  }
  .brand-dot {
    width: 86px;
    height: 86px;
    border-radius: 50%;
    border: 3px solid var(--teal);
    flex: none;
  }
  .brand-name {
    color: var(--ink-grey);
    font-weight: 300;
    text-transform: uppercase;
    line-height: 1.15;
  }
  .brand-name .line-1 {
    display: block;
    font-size: 34px;
    letter-spacing: 4px;
  }
  .brand-name .line-2 {
    display: block;
    font-size: 15px;
    letter-spacing: 9px;
    margin-top: 6px;
    padding-left: 4px;
  }
  .contact-block {
    position: absolute;
    left: 470px;
    top: 260px;
    color: var(--ink-white);
  }
  .person-name {
    font-size: 46px;
    font-weight: 700;
    letter-spacing: 0.3px;
    line-height: 1.1;
  }
  .person-role {
    color: var(--teal);
    font-size: 26px;
    font-weight: 400;
    margin-top: 4px;
    margin-bottom: 22px;
  }
  .contact-list { list-style: none; }
  .contact-list li {
    display: flex;
    align-items: center;
    gap: 14px;
    font-size: 23px;
    font-weight: 400;
    line-height: 1.45;
  }
  .contact-list svg { width: 20px; height: 20px; flex: none; }
  .accent-band {
    position: absolute;
    left: 440px;
    right: 0;
    bottom: 0;
    height: 62px;
    background: linear-gradient(180deg, var(--teal) 0%, var(--teal-deep) 100%);
    border-top-left-radius: 46px;
  }
</style>
</head>
<body>
<main class="stage">
  <section class="card" aria-label="Clear Path Coaching business card, front">
    <div class="brand">
      <span class="brand-dot" aria-hidden="true"></span>
      <p class="brand-name">
        <span class="line-1">Clear Path</span>
        <span class="line-2">Coaching</span>
      </p>
    </div>

    <div class="contact-block">
      <h1 class="person-name">Rebecca Tanfield</h1>
      <p class="person-role">Director</p>
      <ul class="contact-list">
        <li>
          <svg viewBox="0 0 20 20" aria-hidden="true"><path fill="var(--teal)" d="M5.2 1.5l2.6 3.9-1.7 1.9c.9 2.3 2.6 4.2 4.8 5.4l1.8-1.7 3.9 2.5-1.3 3.5C9 16.5 3.4 10.9 2 4.7z"/></svg>
          <span>0491 362 517</span>
        </li>
        <li>
          <svg viewBox="0 0 20 20" aria-hidden="true"><rect x="1.5" y="4" width="17" height="12" rx="1.5" fill="none" stroke="var(--teal)" stroke-width="2"/><path d="M2 5l8 6 8-6" fill="none" stroke="var(--teal)" stroke-width="2"/></svg>
          <span>bec@clearpathcoaching.example.au</span>
        </li>
        <li>
          <svg viewBox="0 0 20 20" aria-hidden="true"><circle cx="10" cy="10" r="8" fill="none" stroke="var(--teal)" stroke-width="2"/><ellipse cx="10" cy="10" rx="3.5" ry="8" fill="none" stroke="var(--teal)" stroke-width="1.6"/><path d="M2 10h16" stroke="var(--teal)" stroke-width="1.6"/></svg>
          <span>www.clearpathcoaching.example.au</span>
        </li>
      </ul>
    </div>

    <div class="accent-band" aria-hidden="true"></div>
  </section>
</main>
</body>
</html>
```